Heritage Hollow Business Cards

Require a business card design. <br/><br/>Needs to include logo (either round or long version) plus these details:<br/>Maya Torvell<br/>Heritage Hollow<br/>maya@kelvadtrading.com.au<br/>02 6481 7395<br/>PO Box Glenwarra NSW 2791<br/>www.heritagehollow.com.au<br/><br/>I need in an editable format so that I can create for multiple staff members. <br/><br/>

Target Market(s)

We are an online store selling renovation products to home owners are builders. Looking for a classic classy design.

Industry/Entity Type

Home And Garden

Contact Information for Business Card

Maya Torvell
Heritage Hollow
maya@kelvadtrading.com.au
02 6481 7395
PO Box Glenwarra NSW 2791
www.heritagehollow.com.au

Colors

Designer to choose colors to be used in the design.

Requirements
Must have
• Must include Logo.

```html
<!DOCTYPE html>
<html lang="en">
<head>
<meta charset="utf-8">
<title>Heritage Hollow Business Cards</title>
<link href="https://fonts.googleapis.com/css2?family=Montserrat:wght@400;500&display=swap" rel="stylesheet">
<style>
  :root {
    --backdrop: #e9e6e1;
    --card-white: #ffffff;
    --card-black: #0b0b0c;
    --ink: #1d1d1d;
    --ink-soft: #444444;
    --accent-green: #2f5a47;
    --logo-ring: #555555;
    --ghost: #2b2b2d;
  }
  * { margin: 0; padding: 0; box-sizing: border-box; }
  html, body {
    width: 1200px; height: 859px; overflow: hidden;
    background: var(--backdrop);
    font-family: "Montserrat", sans-serif;
  }
  .stage { position: relative; width: 1200px; height: 859px; }
  .card {
    position: absolute; top: 281px;
    width: 520px; height: 296px;
    border-radius: 14px; overflow: hidden;
    box-shadow: 0 10px 24px rgba(0,0,0,0.25);
  }
  .card--front { left: 60px; background: var(--card-white); color: var(--ink); }
  .card--back { left: 620px; background: var(--card-black); }

  .logo-badge {
    position: absolute; left: 34px; top: 17px;
    width: 106px; height: 106px; border-radius: 50%;
    border: 1px solid var(--logo-ring);
    display: flex; align-items: center; justify-content: center;
    text-align: center;
  }
  .logo-badge__name {
    font-size: 14px; font-weight: 500; line-height: 1.1; color: var(--ink);
  }
  .edge-dot {
    position: absolute; left: -6px; top: 138px;
    width: 12px; height: 18px; border-radius: 6px;
    background: var(--accent-green);
  }
  .person-name {
    position: absolute; left: 24px; top: 128px;
    font-size: 22px; font-weight: 500; letter-spacing: 0.2px;
  }
  .name-rule {
    position: absolute; left: 24px; top: 170px;
    width: 162px; height: 1.5px; background: var(--accent-green);
  }
  .address {
    position: absolute; left: 24px; top: 180px;
    font-size: 13px; line-height: 18px; color: var(--ink-soft); font-weight: 400;
  }
  .contact-list {
    position: absolute; left: 24px; top: 226px;
    list-style: none; font-size: 13px; color: var(--ink-soft);
  }
  .contact-list li { display: flex; align-items: center; gap: 7px; height: 18.5px; }
  .contact-list svg { width: 12px; height: 12px; flex: none; }

  .front-sketch {
    position: absolute; left: 247px; top: 61px;
    width: 273px; height: 235px;
    background: linear-gradient(215deg, #9a9a9a 0%, #d9d9d9 45%, #ffffff 80%);
    clip-path: polygon(100% 0, 100% 100%, 0 100%);
  }
  .back-sketch {
    position: absolute; left: 0; top: 72px;
    width: 273px; height: 186px;
    background: linear-gradient(160deg, #8a8a8a 0%, #3a3a3a 55%, #0b0b0c 100%);
    clip-path: polygon(0 0, 100% 100%, 0 100%);
  }
  .ghost-badge {
    position: absolute; left: 288px; top: 42px;
    width: 178px; height: 178px; border-radius: 50%;
    border: 1px solid var(--ghost);
    display: flex; align-items: center; justify-content: center; text-align: center;
  }
  .ghost-badge__name {
    font-size: 24px; font-weight: 500; line-height: 1.1; color: var(--ghost);
  }
</style>
</head>
<body>
<main class="stage">
  <section class="card card--front" aria-label="Business card front">
    <div class="logo-badge"><span class="logo-badge__name">Heritage<br>Hollow</span></div>
    <span class="edge-dot"></span>
    <h1 class="person-name">Maya Torvell</h1>
    <div class="name-rule"></div>
    <p class="address">PO Box Glenwarra<br>NSW 2791</p>
    <ul class="contact-list">
      <li>
        <svg viewBox="0 0 12 12" fill="none" stroke="var(--accent-green)" stroke-width="1.2"><circle cx="6" cy="6" r="5"/><path d="M4 3.6l1 1.2-.6.8c.4.8 1 1.4 1.8 1.8l.8-.6 1.2 1-.7.9C5.6 8.6 3.6 6.6 3.3 4.3z" fill="var(--accent-green)" stroke="none"/></svg>
        02 6481 7395
      </li>
      <li>
        <svg viewBox="0 0 12 12" fill="none" stroke="var(--accent-green)" stroke-width="1.1"><rect x="1" y="2.5" width="10" height="7"/><path d="M1 2.5l5 4 5-4"/></svg>
        maya@kelvadtrading.com.au
      </li>
      <li>
        <svg viewBox="0 0 12 12" fill="var(--accent-green)"><circle cx="6" cy="6" r="5.5"/><path d="M1 6h10M6 .5c-2 2.5-2 8.5 0 11M6 .5c2 2.5 2 8.5 0 11" stroke="#fff" stroke-width=".7" fill="none"/></svg>
        www.heritagehollow.com.au
      </li>
    </ul>
    <div class="front-sketch" role="img" aria-label="Hand-drawn ink sketch of a roof gable with cross-hatched shading"></div>
  </section>

  <section class="card card--back" aria-label="Business card back">
    <div class="back-sketch" role="img" aria-label="White chalk-style sketch of a roof gable with a chimney"></div>
    <div class="ghost-badge"><span class="ghost-badge__name">Heritage<br>Hollow</span></div>
  </section>
</main>
</body>
</html>
```